Design für Auto-Folierung, Lieferwagen Tischlerei

Design für Lieferwagen Hollvik Traganer mit Kofferaufbau.
(Hollvik Traganer 284LXT Koffer 4325 Farbe weiß, Baujahr 2020)
Es sollte vom Design zu Holz, Möbel, Tischler, Firmenlogo passen.
Farben sollten zum Firmenlogo und der Wagenfarbe passen.
Es sollte modern und zeitlos sein.
Zusätzlicher Text und Bilder können verwendet werden.
Es würde vermutlich reichen den Aufbau und Motorhaube zu folieren, bin aber für alles offen.
Integriert werden sollte: Firmenlogo (rundum) und Anschrift (hinten) .

Requirements
Must have
• Logo, Anschrift

```html
<!DOCTYPE html>
<html lang="de">
<head>
<meta charset="utf-8">
<title>Korven Tischlerei – Fahrzeugbeschriftung</title>
<link rel="stylesheet" href="https://fonts.googleapis.com/css2?family=Michroma&family=Oswald:wght@600&family=Poppins:wght@500;600&display=swap">
<style>
  :root {
    --bg: #ecedef;
    --panel: #ffffff;
    --panel-edge: #d9dbdf;
    --navy: #1b1f4b;
    --gold: #c9a43a;
    --gold-soft: #b89a55;
    --wood-light: #d9b27a;
    --wood-mid: #a9763f;
    --wood-dark: #6e4522;
  }
  * { box-sizing: border-box; margin: 0; padding: 0; }
  html, body { width: 1200px; height: 1200px; overflow: hidden; }
  body { background: var(--bg); position: relative; }

  .box-side {
    position: absolute; left: 40px; top: 390px;
    width: 820px; height: 418px;
    background: var(--panel);
    border: 1px solid var(--panel-edge);
    overflow: hidden;
  }
  .brand-mark {
    position: absolute; left: 117px; top: 40px;
    width: 150px; height: 150px;
    background: var(--gold);
  }
  .brand-name {
    position: absolute; left: 300px; top: 50px;
    font-family: "Michroma", sans-serif;
    font-weight: 400;
    line-height: 1;
    white-space: nowrap;
  }
  .brand-name .name-main {
    display: block; font-size: 70px; letter-spacing: 2px;
    color: var(--navy);
  }
  .brand-name .name-sub {
    display: block; font-size: 33px; letter-spacing: 3px;
    margin-top: 22px; color: var(--gold);
  }

  .furniture-scene {
    position: absolute; left: 0; top: 222px;
    width: 100%; height: 196px;
    background: linear-gradient(180deg,
      rgba(217,178,122,0) 0%,
      rgba(217,178,122,0.55) 38%,
      var(--wood-mid) 55%,
      var(--wood-dark) 100%);
  }
  .services {
    position: absolute; left: 130px; top: 372px;
    font-family: "Oswald", sans-serif; font-weight: 600;
    font-size: 15px; letter-spacing: 0.5px;
    color: var(--navy);
    display: flex; gap: 8px; align-items: center;
    white-space: nowrap;
  }
  .services .dot { width: 5px; height: 5px; border-radius: 50%; background: var(--panel); }

  .cab-door {
    position: absolute; left: 900px; top: 450px;
    width: 260px; height: 358px;
    background: var(--panel);
    border: 1px solid var(--panel-edge);
  }
  .contact {
    position: absolute; left: 24px; top: 196px;
    font-family: "Poppins", sans-serif;
    color: var(--gold-soft);
    white-space: nowrap;
  }
  .contact .phone { font-weight: 600; font-size: 19px; letter-spacing: 0.5px; }
  .contact .web { font-weight: 500; font-size: 13.5px; margin-top: 2px; }
</style>
</head>
<body>
  <section class="box-side">
    <div class="brand-mark"></div>
    <h1 class="brand-name">
      <span class="name-main">KORVEN</span>
      <span class="name-sub">TISCHLEREI</span>
    </h1>
    <div class="furniture-scene" role="img" aria-label="Holzmöbel – Stühle, Tisch, Kommode und Hocker – auf einem Boden aus Holzdielen"></div>
    <p class="services">
      <span>KÜCHE</span><span class="dot"></span>
      <span>ESSZIMMER</span><span class="dot"></span>
      <span>WOHNZIMMER</span><span class="dot"></span>
      <span>SCHLAFZIMMER</span><span class="dot"></span>
      <span>BAD</span><span class="dot"></span>
      <span>VERSCHIEDENES</span>
    </p>
  </section>

  <section class="cab-door">
    <div class="contact">
      <p class="phone">+43 660 5187342</p>
      <p class="web">www.korven-tischlerei.at</p>
    </div>
  </section>
</body>
</html>
```